6 page (for now) squarespace website design for a Mobile Fitness small business

My sons California based small business "BrenVale Coaching" with new subsidiary called "BrenVale 4 Kids". I don't understand coding the website, is that the function squarespace provides?
In the end I want a working website, squarespace, I have a google workspace domain, email and subscription to squarespace & google workspace. URLs include brenvalecoaching.example and brenvale4kids.example. I have an idea of what I am looking for in a website and I have some examples of website designs I like, but I am 100% open to your design concepts and artistic flair. email is torin@brenvalecoaching.example
I am looking for someone to design the site, help me understand how to make "minor" changes and hopefully have a long term relationship on the tech side of the business. I need an Idea of pricing for future changes (Rate T&M).
There are 2 businesses so I need a way to incorporate both the main company and a subsidiary into 1 website or link it somehow. I am open to your suggestions how to accomplish that. Do I need 2 completely separate websites or can it be done on 1 site directing you to different pages. I read conflicting info if it is a BAD idea to link 2 different websites so I will defer to your advice.
Below are the pages I need designed:
- Home Page- BrenVale Coaching
- Home Page- BrenVale 4 Kids (Homeschool market)
- Member Page (subscription service?)
- Workouts- with video clips 1-6 min each
- About
- Contact
- FAQ's
Future work & page designs:
- Store with training subscriptions & a few merch items
- Booking Appointments
- Bookshelf
- email campaign
-Blog
I like the feel of this website:
https://zestlope.example/

```html
<!DOCTYPE html>
<html lang="en">
<head>
<meta charset="utf-8">
<title>BrenVale Coaching — Workouts</title>
<link rel="stylesheet" href="https://fonts.googleapis.com/css2?family=Montserrat:wght@400;500;600;700&family=Rajdhani:wght@700&display=swap">
<style>
:root{
  --ink:#111214;
  --nav-bg:#1f2023;
  --nav-link:#8a8c90;
  --accent:#f7931e;
  --accent-deep:#f15a24;
  --teal:#2bb3a0;
  --page:#f5f5f5;
  --card:#ffffff;
  --text:#555759;
  --footer:#151515;
  --rule:#c9c9c9;
}
*{margin:0;padding:0;box-sizing:border-box}
html,body{width:1200px;height:2609px;overflow:hidden}
body{position:relative;background:var(--page);font-family:"Montserrat",sans-serif;color:var(--ink)}
.abs{position:absolute}
.display{font-family:"Rajdhani",sans-serif;font-weight:700;text-transform:uppercase}

/* header */
.site-header{left:0;top:0;width:1200px;height:63px;background:var(--nav-bg)}
.brand{left:45px;top:12px;display:flex;align-items:center;gap:14px}
.brand-dot{width:40px;height:40px;border-radius:50%;background:#fff}
.brand-name{color:#fff;font-size:25px;font-weight:500;letter-spacing:5px}
.main-nav{left:382px;top:26px;display:flex;gap:30px;font-size:10.5px;letter-spacing:2.4px;color:var(--nav-link);font-weight:500}
.main-nav .current{color:#fff;font-weight:700;border-bottom:2px solid var(--accent);padding-bottom:6px}
.header-social{left:1093px;top:27px;display:flex;gap:14px}
.header-social span{width:10px;height:10px;border-radius:50%;background:var(--nav-link)}

/* hero */
.hero{left:0;top:63px;width:1200px;height:452px;background:radial-gradient(ellipse at 45% 45%,#3a3836 0%,#1c1b1a 55%,#0d0d0d 100%)}
.hero-title{left:0;top:230px;width:1200px;text-align:center;color:#fff;font-size:62px;letter-spacing:1px}

/* class cards */
.class-card{top:578px;width:321px;height:375px;background:var(--card);text-align:center}
.class-photo{width:100%;height:162px}
.class-card h3{margin-top:27px;font-size:12.5px;font-weight:700;letter-spacing:.5px}
.class-meta{margin-top:13px;font-size:8.5px;color:var(--text)}
.class-card p{margin:15px auto 0;width:270px;font-size:10px;line-height:15px;color:var(--text)}
.btn{display:inline-block;background:var(--ink);color:#fff;font-size:9px;font-weight:700;letter-spacing:.4px;text-transform:uppercase;text-align:center}
.class-card .btn{position:absolute;left:98px;top:315px;width:125px;height:28px;line-height:28px}
.btn-warm{background:linear-gradient(90deg,var(--accent-deep),var(--accent))}

.section-rule{left:100px;top:1028px;width:1000px;height:2px;background:var(--rule)}

/* videos */
.videos-title{left:0;top:1106px;width:1200px;text-align:center;font-size:34px}
.videos-sub{left:0;top:1163px;width:1200px;text-align:center;font-size:12px;letter-spacing:.5px;color:var(--text)}
.feature-panel{left:100px;top:1226px;width:486px;height:536px;background:var(--card)}
.feature-video{left:14px;top:19px;width:459px;height:267px;background:linear-gradient(160deg,#5c6068 0%,#33363b 50%,#1c1e22 100%)}
.feature-panel h3{position:absolute;left:24px;top:312px;font-size:18px;font-weight:600;color:#444}
.feature-copy{position:absolute;left:24px;top:347px;width:440px;font-size:11px;line-height:19px;color:var(--text)}
.feature-copy p+p{margin-top:12px}
.feature-panel .btn{position:absolute;left:24px;top:479px;width:125px;height:29px;line-height:29px}

.controls{position:absolute;left:0;bottom:0;width:100%;height:18px;display:flex;align-items:center;gap:8px;padding:0 6px}
.play{width:28px;height:14px;background:#2b2d31;display:flex;align-items:center;justify-content:center}
.play::after{content:"";border-left:7px solid #fff;border-top:4px solid transparent;border-bottom:4px solid transparent}
.track{flex:1;height:4px;background:#5a5d62}
.track i{display:block;width:45%;height:100%;background:#1ea5e0}
.feature-video .controls{height:40px;padding:0 12px}
.feature-video .play{width:58px;height:32px}
.feature-video .play::after{border-left-width:13px;border-top-width:8px;border-bottom-width:8px}

.thumb{width:232px}
.thumb-media{position:relative;height:135px}
.thumb h4{margin-top:17px;font-size:12.5px;font-weight:600;color:#555;letter-spacing:.3px}

/* CTA */
.cta{left:0;top:1890px;width:1200px;height:437px;background:radial-gradient(ellipse at 50% 55%,#3b2d25 0%,#1a1614 40%,#050505 75%)}
.cta-text{left:0;top:1978px;width:1200px;text-align:center;font-size:64px;line-height:63px;color:#fff}
.cta-text .warm{color:var(--accent)}
.cta .btn{position:absolute;left:521px;top:356px;width:158px;height:41px;line-height:41px;font-size:13px;font-weight:600;letter-spacing:.3px}

/* footer */
.site-footer{left:0;top:2327px;width:1200px;height:282px;background:var(--footer);color:#fff}
.foot-col{top:45px}
.foot-col h5{font-size:10.5px;font-weight:700;font-style:italic;letter-spacing:.5px}
.foot-col h5::after{content:"";display:block;width:20px;height:2px;background:var(--teal);margin-top:5px}
.foot-col p{margin-top:22px;font-size:12px;letter-spacing:.3px}
.foot-social{display:flex;gap:20px;margin-top:20px}
.foot-social span{width:15px;height:15px;border-radius:50%;background:#bdbdbd}
.foot-brand{left:0;top:138px;width:1200px;text-align:center}
.foot-brand .brand-dot{margin:0 auto;width:50px;height:50px}
.foot-brand .brand-name{display:block;margin-top:14px;font-size:19px;letter-spacing:4px}
.foot-nav{left:0;top:244px;width:1200px;display:flex;justify-content:center;gap:30px;font-size:10px;letter-spacing:2.4px;color:#7a7c80}
</style>
</head>
<body>

<header class="abs site-header">
  <div class="abs brand"><span class="brand-dot"></span><span class="brand-name">BRENVALE</span></div>
  <nav class="abs main-nav">
    <span>HOME</span><span>ABOUT</span><span class="current">WORKOUTS</span><span>MEMBERSHIP</span><span>SHOP</span><span>CONTACT</span>
  </nav>
  <div class="abs header-social"><span></span><span></span><span></span><span></span></div>
</header>

<section class="abs hero" role="img" aria-label="Dark close-up photo of chalked hands clapping"></section>
<h1 class="abs display hero-title">Workouts</h1>

<article class="abs class-card" style="left:100px">
  <div class="class-photo" role="img" aria-label="Photo of a boxer training by the sea" style="background:linear-gradient(180deg,#9cc3e0 0%,#3f7fa8 55%,#6b7a3c 100%)"></div>
  <h3>MARTIAL ARTS</h3>
  <div class="class-meta">09:00 - 11:00 | TORIN VALE</div>
  <p>Lorem ipsum dolor sit amet, consectetuer adipiscing elit, sed diam nonummy nibh euismod tincidunt ut laoreet dolore magna aliquam erat volutpat.</p>
  <span class="btn">Read More</span>
</article>
<article class="abs class-card" style="left:440px">
  <div class="class-photo" role="img" aria-label="Photo of a woman running at sunset" style="background:linear-gradient(180deg,#f7e3c4 0%,#e7b77d 55%,#8d6a48 100%)"></div>
  <h3>RUNNING</h3>
  <div class="class-meta">09:00 - 11:00 | TORIN VALE</div>
  <p>Lorem ipsum dolor sit amet, consectetuer adipiscing elit, sed diam nonummy nibh euismod tincidunt ut laoreet dolore magna aliquam erat volutpat.</p>
  <span class="btn btn-warm">Read More</span>
</article>
<article class="abs class-card" style="left:779px">
  <div class="class-photo" role="img" aria-label="Photo of a group meditating on mats in a forest" style="background:linear-gradient(180deg,#4f6b2e 0%,#7d8a55 50%,#6a5a45 100%)"></div>
  <h3>MEDITATION</h3>
  <div class="class-meta">09:00 - 11:00 | TORIN VALE</div>
  <p>Lorem ipsum dolor sit amet, consectetuer adipiscing elit, sed diam nonummy nibh euismod tincidunt ut laoreet dolore magna aliquam erat volutpat.</p>
  <span class="btn">Read More</span>
</article>

<div class="abs section-rule"></div>

<h2 class="abs display videos-title">Watch Our Videos</h2>
<div class="abs videos-sub">LOREM IPSUM DOLOR SIT AMET</div>

<article class="abs feature-panel">
  <div class="abs feature-video" role="img" aria-label="Intro video still of a trainer working out in a gym">
    <div class="controls"><span class="play"></span><span class="track"><i></i></span></div>
  </div>
  <h3>Introduction</h3>
  <div class="feature-copy">
    <p>Lorem ipsum dolor sit amet, consectetuer adipiscing elit, sed diam nonummy nibh euismod tincidunt ut laoreet dolore magna aliquam erat volutpat.</p>
    <p>Ut wisi enim ad minim veniam, quis nostrud exerci tation ullamcorper suscipit lobortis nisl ut aliquip ex ea commodo consequat. Duis autem vel eum iriure dolor in hendrerit in vulputate velit esse molestie consequat, vel illum dolore eu</p>
  </div>
  <span class="btn">Read More</span>
</article>

<div class="abs thumb" style="left:613px;top:1227px">
  <div class="thumb-media" role="img" aria-label="Video still of people on treadmills" style="background:linear-gradient(135deg,#d9d4cc,#8d8f92)"><div class="controls"><span class="play"></span><span class="track"><i></i></span></div></div>
  <h4>Workout Video 01</h4>
</div>
<div class="abs thumb" style="left:868px;top:1227px">
  <div class="thumb-media" role="img" aria-label="Video still of a spin class" style="background:linear-gradient(135deg,#d85a8a,#e9e4dd 55%,#3aa0d8)"><div class="controls"><span class="play"></span><span class="track"><i></i></span></div></div>
  <h4>Workout Video 02</h4>
</div>
<div class="abs thumb" style="left:613px;top:1417px">
  <div class="thumb-media" role="img" aria-label="Video still of a woman on a leg machine" style="background:linear-gradient(135deg,#5a4a48,#8c2f3a 50%,#c9c3bd)"><div class="controls"><span class="play"></span><span class="track"><i></i></span></div></div>
  <h4>Workout Video 03</h4>
</div>
<div class="abs thumb" style="left:868px;top:1417px">
  <div class="thumb-media" role="img" aria-label="Video still of a trainer coaching a client" style="background:linear-gradient(135deg,#b9b6b0,#6d7074 55%,#2f6fc0)"><div class="controls"><span class="play"></span><span class="track"><i></i></span></div></div>
  <h4>Workout Video 04</h4>
</div>
<div class="abs thumb" style="left:613px;top:1607px">
  <div class="thumb-media" role="img" aria-label="Video still of a man lifting weights" style="background:linear-gradient(135deg,#8a8a86,#3a3b3e 60%,#1d1e20)"><div class="controls"><span class="play"></span><span class="track"><i></i></span></div></div>
  <h4>Workout Video 05</h4>
</div>
<div class="abs thumb" style="left:868px;top:1607px">
  <div class="thumb-media" role="img" aria-label="Video still of a partner stretching class" style="background:linear-gradient(135deg,#e8e2da,#3b6fc8 50%,#c45a4e)"><div class="controls"><span class="play"></span><span class="track"><i></i></span></div></div>
  <h4>Workout Video 06</h4>
</div>

<section class="abs cta" role="img" aria-label="Dark photo of a muscular athlete gripping a barbell">
  <span class="btn btn-warm">BOOK SESSION</span>
</section>
<div class="abs display cta-text">Lorem<br>Ipsum<br><span class="warm">Dolor<br>Sit Amet</span></div>

<footer class="abs site-footer">
  <div class="abs foot-col" style="left:267px"><h5>MOBILE</h5><p>(555) 014-2298</p></div>
  <div class="abs foot-col" style="left:520px"><h5>EMAIL</h5><p>torin@brenvalecoaching.example</p></div>
  <div class="abs foot-col" style="left:772px"><h5>SOCIAL</h5><div class="foot-social"><span></span><span></span><span></span><span></span></div></div>
  <div class="abs foot-brand"><div class="brand-dot"></div><span class="brand-name">BRENVALE</span></div>
  <nav class="abs foot-nav"><span>HOME</span><span>ABOUT</span><span>WORKOUTS</span><span>MEMBERSHIP</span><span>SHOP</span><span>CONTACT</span></nav>
</footer>

</body>
</html>
```